Change of trading name, rebrand

existing website to be updated with new theme and logo. existing website is
www.harlowbrentmere.com.au
Industry/Entity Type
Construction
Coding
Coded - Design and coding required
Number of Pages Required
5+ page
Requirements
Must have
- be mobile phone friendly

```html
<!DOCTYPE html>
<html lang="en">
<head>
<meta charset="utf-8">
<meta name="viewport" content="width=device-width, initial-scale=1">
<title>HBR Plant Hire</title>
<link href="https://fonts.googleapis.com/css2?family=Krona+One&family=Roboto:wght@400;500;700&display=swap" rel="stylesheet">
<style>
:root{
  --navy:#25276f;
  --navy-dark:#1c1d58;
  --ink:#222;
  --muted:#444;
  --lilac:#e3e3f3;
  --paper:#f1f1f3;
  --line:#d4d4dc;
  --white:#fff;
  --black:#000;
}
*{box-sizing:border-box;margin:0;padding:0}
html,body{width:1200px;height:4035px;overflow:hidden}
body{position:relative;font-family:"Roboto",sans-serif;color:var(--ink);background:var(--white)}
.display{font-family:"Krona One",sans-serif;text-transform:uppercase;letter-spacing:1px}
.abs{position:absolute}

/* top bar */
.topbar-left{left:0;top:0;width:470px;height:41px;background:var(--navy);clip-path:polygon(0 0,100% 0,96% 100%,0 100%);color:#fff;font-size:15px;display:flex;align-items:center;padding-left:75px;gap:10px}
.topbar-right{left:744px;top:0;width:456px;height:41px;background:var(--navy);clip-path:polygon(0 0,100% 0,100% 100%,4% 100%);color:#fff;font-size:15px;display:flex;align-items:center;padding-left:60px;gap:8px}
.topbar-left b,.topbar-right b{font-weight:700}
.nav{top:41px;left:0;width:1200px;height:72px;font-size:15px}
.nav a{position:absolute;top:32px;color:var(--ink);text-decoration:none}
.nav a.active{color:var(--navy);text-decoration:underline}
.brand{left:518px;top:8px;width:164px;height:100px;text-align:center}
.brand .mark{width:40px;height:40px;background:var(--navy);margin:4px auto 6px}
.brand .name{font-family:"Krona One",sans-serif;color:var(--navy);font-size:14px;line-height:1.3}
.btn-contact{left:915px;top:56px;width:215px;height:43px;border:2px solid var(--navy);display:flex;align-items:center;justify-content:center;gap:10px;color:var(--navy);font-family:"Krona One",sans-serif;font-size:13px}

/* hero */
.hero{top:113px;left:0;width:1200px;height:592px;overflow:hidden}
.hero-photo{position:absolute;inset:0;background:linear-gradient(180deg,#4f88c8 0%,#8fb6de 40%,#9a8a72 62%,#6e5e4a 100%)}
.hero-copy{position:absolute;left:0;right:0;top:143px;text-align:center;color:#fff}
.hero-copy .kicker{font-weight:700;font-size:18px}
.hero-copy h1{font-family:"Krona One",sans-serif;font-size:33px;line-height:44px;margin-top:12px;font-weight:400}
.hero-copy p{font-size:14px;line-height:24px;width:460px;margin:14px auto 0}
.hero-btn{position:absolute;left:497px;top:379px;width:206px;height:44px;border:2px solid #fff;color:#fff;font-family:"Krona One",sans-serif;font-size:14px;display:flex;align-items:center;justify-content:center}
.round{position:absolute;width:40px;height:40px;border-radius:50%;background:#fff;display:flex;align-items:center;justify-content:center}
.round.navy{background:var(--navy)}
.hero-shape{position:absolute;left:0;top:0}

/* welcome */
.welcome-mark{left:94px;top:783px;width:470px;height:329px;display:flex;flex-direction:column;align-items:center;justify-content:center;gap:18px}
.welcome-mark .art{width:430px;height:200px;background:linear-gradient(180deg,#d8d8e6,#b9b9cc)}
.welcome-mark .name{font-family:"Krona One",sans-serif;font-size:40px;color:var(--navy)}
.welcome-text{left:642px;top:779px;width:460px}
.welcome-text h2{font-size:30px;line-height:40px;color:var(--navy);font-weight:400}
.welcome-text .lead{color:var(--navy);font-weight:500;font-size:17px;line-height:26px;margin-top:14px}
.welcome-text .body{font-size:14.5px;line-height:25.5px;color:var(--muted);margin-top:14px}
.btn-navy{background:var(--navy);color:#fff;font-family:"Krona One",sans-serif;font-size:14px;display:flex;align-items:center;justify-content:center}

/* features */
.features{top:1230px;left:0;width:1200px;height:376px;background:var(--lilac)}
.feature{position:absolute;top:127px;width:193px;height:138px;background:#fff;border:2px solid #cfcfdf;text-align:center;color:var(--navy);font-size:15px;line-height:22px;padding-top:62px}
.feature.on{background:var(--navy);color:#fff;border-color:var(--navy)}
.feature strong{display:block;font-family:"Krona One",sans-serif;font-size:18px;line-height:26px;font-weight:400}
.feature .badge{position:absolute;left:50%;top:-47px;margin-left:-47px;width:94px;height:94px;border-radius:50%;background:var(--navy);border:4px solid #fff;display:flex;align-items:center;justify-content:center}

/* services */
.services{top:1606px;left:0;width:1200px;height:906px;overflow:hidden}
.services-bg{position:absolute;inset:0;background:linear-gradient(180deg,#3f6fb4 0%,#7ea4d4 40%,#a98d6b 62%,#7a5d3f 100%)}
.services h2{position:absolute;top:117px;width:100%;text-align:center;color:#fff;font-size:28px;font-weight:400}
.tile{position:absolute;width:291px}
.photo{background:linear-gradient(160deg,#c38a4a,#8d6a45)}
.svc-card{background:#fff;text-align:center;padding:34px 18px 0}
.svc-card h3{font-family:"Krona One",sans-serif;font-size:15px;color:var(--navy);font-weight:400;margin-top:14px}
.svc-card p{font-size:12.5px;line-height:20px;color:#333;margin-top:10px}
.svc-dark{background:var(--navy);color:#fff;text-align:center;padding:58px 26px 0;font-size:13px;line-height:20px}
.svc-dark h3{font-family:"Krona One",sans-serif;font-size:15px;font-weight:400;margin-top:10px}
.notch-up{position:absolute;top:-14px;left:50%;margin-left:-14px;width:0;height:0;border-left:14px solid transparent;border-right:14px solid transparent;border-bottom:14px solid #fff}
.notch-down{position:absolute;bottom:-14px;left:50%;margin-left:-14px;width:0;height:0;border-left:14px solid transparent;border-right:14px solid transparent;border-top:14px solid var(--navy)}
.mini{position:absolute;left:50%;width:36px;height:36px;margin-left:-18px;border-radius:50%;background:#fff;border:2px solid var(--navy);display:flex;align-items:center;justify-content:center}

/* clients */
.clients-title{top:2588px;width:1200px;text-align:center;color:var(--navy);font-size:28px;font-weight:400}
.clients{top:2661px;left:60px;width:1089px;height:74px;display:flex;border:1px solid var(--line)}
.client{flex:1;display:flex;align-items:center;justify-content:center;border-right:1px solid var(--line);font-size:20px;font-weight:500;color:#555;gap:8px}
.client:last-child{border-right:0}
.client.on{border:2px solid var(--navy);box-shadow:0 3px 10px rgba(0,0,0,.25)}
.client i{width:12px;height:12px;background:#777;display:inline-block}
.pager{position:absolute;top:2778px;width:38px;height:38px;border-radius:50%;border:2px solid #999;background:#fff;display:flex;align-items:center;justify-content:center}

/* contact */
.contact{top:2899px;left:0;width:1200px;height:770px;background:var(--paper)}
.contact h2{position:absolute;top:118px;width:100%;text-align:center;color:var(--navy);font-size:30px;line-height:38px;font-weight:400}
.contact h2 span{color:var(--black)}
.info{position:absolute;left:130px;display:flex;gap:22px}
.info .ic{width:42px;height:42px;border-radius:50%;background:var(--navy);display:flex;align-items:center;justify-content:center;flex:none}
.info h4{font-family:"Krona One",sans-serif;color:var(--navy);font-size:14.5px;font-weight:400}
.info p{font-size:14.5px;color:#333;margin-top:10px}
.field{position:absolute;background:#fff;border:1px solid #e2e2e6;box-shadow:0 1px 4px rgba(0,0,0,.06);font-size:13px;color:#333;padding:17px 17px}

/* footer */
.footer{top:3667px;left:0;width:1200px;height:368px;background:var(--black);color:#fff}
.footer h5{font-family:"Krona One",sans-serif;font-size:14px;font-weight:400;position:absolute;top:52px;line-height:20px}
.footer ul{list-style:none;position:absolute;top:92px;font-size:14px;line-height:30px}
.f-brand{left:107px;top:83px;width:230px;height:167px;display:flex;flex-direction:column;align-items:center;justify-content:center;gap:10px}
.f-brand .art{width:200px;height:95px;background:linear-gradient(180deg,#3a3a3a,#1f1f1f)}
.f-brand .name{font-family:"Krona One",sans-serif;font-size:22px}
.f-row{position:absolute;left:592px;display:flex;align-items:center;gap:14px;font-size:14px;line-height:24px}
.f-row .ic{width:40px;height:40px;border-radius:50%;border:2px solid #fff;display:flex;align-items:center;justify-content:center;flex:none}
.social{position:absolute;top:166px;width:26px;height:26px;border-radius:50%;border:2px solid #fff}
.social.on{border-color:var(--navy);background:#2e3990;width:32px;height:32px;top:163px}
.copy{position:absolute;top:326px;width:100%;text-align:center;font-size:12px}
</style>
</head>
<body>

<!-- top bar -->
<div class="abs topbar-left">
  <svg width="20" height="20" viewBox="0 0 24 24" fill="none" stroke="#fff" stroke-width="1.6"><circle cx="12" cy="12" r="10"/><path d="M9 7l2 2-1.5 1.5a6 6 0 0 0 3 3L14 12l2 2-1.5 2A8 8 0 0 1 7 8.5z"/></svg>
  <span>Call Us Today : <b>1300 555 019</b></span>
</div>
<div class="abs topbar-right">
  <svg width="16" height="14" viewBox="0 0 24 18" fill="none" stroke="#fff" stroke-width="2"><rect x="1" y="1" width="22" height="16"/><path d="M1 1l11 9 11-9"/></svg>
  <span>Email Us : <b>info@harlowbrentmere.com.au</b></span>
</div>

<!-- nav -->
<nav class="abs nav">
  <a class="active" style="left:80px">Home</a>
  <a style="left:149px">About us</a>
  <a style="left:231px">Plant Hire</a>
  <a style="left:318px">Major Project Snapshot</a>
  <a style="left:764px">Policies</a>
  <a style="left:839px">Jobs</a>
</nav>
<div class="abs brand">
  <div class="mark"></div>
  <div class="name">HBR<br>Plant Hire</div>
</div>
<div class="abs btn-contact">
  <svg width="24" height="20" viewBox="0 0 24 20" fill="none" stroke="#25276f" stroke-width="1.8"><rect x="2" y="3" width="20" height="14"/><path d="M2 3l10 8 10-8"/></svg>
  CONTACT US
</div>

<!-- hero -->
<section class="abs hero">
  <div class="hero-photo" role="img" aria-label="Orange tracked excavator on a dirt worksite under a blue sky"></div>
  <div class="hero-copy">
    <div class="kicker">Committed To Superior Quality Plant Hire Services</div>
    <h1>HBR HEAVY<br>EQUIPMENT HIRE</h1>
    <p>Harlow Brentmere Heavy Equipment Hire specialise in the hire of heavy earthmoving, mining and construction machines with specialised attachments and tooling.</p>
  </div>
  <div class="hero-btn">GET STARTED</div>
  <div class="round" style="left:35px;top:232px"><svg width="14" height="14" viewBox="0 0 14 14"><path d="M9 2L4 7l5 5" stroke="#25276f" stroke-width="2.4" fill="none"/></svg></div>
  <div class="round navy" style="left:1127px;top:232px"><svg width="14" height="14" viewBox="0 0 14 14"><path d="M5 2l5 5-5 5" stroke="#fff" stroke-width="2.4" fill="none"/></svg></div>
  <svg class="hero-shape" width="1200" height="592" viewBox="0 0 1200 592">
    <path d="M0 443 Q600 600 1200 443 L1200 592 L0 592 Z" fill="#fff"/>
    <path d="M110 476 Q380 555 600 568 Q900 545 1200 440 L1200 466 Q900 568 622 580 L600 590 L578 580 Q380 570 110 482 Z" fill="#25276f"/>
  </svg>
</section>

<!-- welcome -->
<div class="abs welcome-mark">
  <div class="art" role="img" aria-label="Line illustration of a tractor and an excavator above the company wordmark"></div>
  <div class="name">HBR Plant Hire</div>
</div>
<div class="abs welcome-text">
  <h2 class="display">Welcome to HBR Plant Hire</h2>
  <p class="lead">Harlow Brentmere Resources Pty Ltd trading as HBR Heavy Equipment is a privately owned company that was established in 2010.</p>
  <p class="body">Our founder saw a need in the market for a plant and equipment supplier who was committed to the successful delivery of client's projects. With this vision and focus HBR has successfully seen our clients deliver on-time and on- budget. Taking the time to under-stand our clients requirements and what they are trying to achieve has allowed HBR to mature into the company it is today.</p>
</div>
<div class="abs btn-navy" style="left:641px;top:1119px;width:168px;height:45px">READ MORE</div>

<!-- features -->
<section class="abs features">
  <div class="feature" style="left:71px"><span class="badge"><svg width="44" height="44" viewBox="0 0 44 44" fill="none" stroke="#fff" stroke-width="2"><circle cx="22" cy="16" r="9"/><path d="M8 40c2-10 26-10 28 0"/><path d="M13 14h18"/></svg></span><strong>20+</strong>Years Of Experience</div>
  <div class="feature" style="left:287px"><span class="badge"><svg width="46" height="40" viewBox="0 0 46 40" fill="none" stroke="#fff" stroke-width="2"><rect x="4" y="18" width="20" height="10"/><path d="M24 20l10-12 8 8"/><rect x="4" y="30" width="24" height="6" rx="3"/></svg></span><strong>100+</strong>Machines In Fleet</div>
  <div class="feature on" style="left:503px"><span class="badge"><svg width="40" height="44" viewBox="0 0 40 44" fill="none" stroke="#fff" stroke-width="2"><path d="M14 4l4 12 6-2 6 26H8l4-20z"/></svg></span>One Of Qld's Largest Suppliers</div>
  <div class="feature" style="left:721px;padding-top:72px"><span class="badge"><svg width="44" height="44" viewBox="0 0 44 44" fill="none" stroke="#fff" stroke-width="2"><circle cx="22" cy="22" r="14"/><circle cx="22" cy="22" r="6"/><path d="M22 4v6M22 34v6M4 22h6M34 22h6"/></svg></span>Onsite Servicing</div>
  <div class="feature" style="left:937px"><span class="badge"><svg width="40" height="46" viewBox="0 0 40 46" fill="none" stroke="#fff" stroke-width="2"><path d="M8 6h24v8H8zM12 14h16l-4 14h-8zM20 28v14"/></svg></span>Custom Machine Attachments</div>
</section>

<!-- services -->
<section class="abs services">
  <div class="services-bg" role="img" aria-label="Fleet of yellow dozers and dump trucks parked on a dirt yard"></div>
  <h2 class="display">Our Services</h2>

  <div class="tile photo" style="left:165px;top:216px;height:278px" role="img" aria-label="Excavator working beside a school building"></div>
  <div class="tile svc-card" style="left:165px;top:494px;height:274px">
    <span class="notch-up"></span>
    <svg width="66" height="56" viewBox="0 0 66 56" fill="none" stroke="#25276f" stroke-width="2.2"><rect x="6" y="26" width="26" height="14"/><path d="M32 28l16-18 12 12-6 8"/><rect x="4" y="42" width="34" height="10" rx="5"/></svg>
    <h3>Excavator Hire</h3>
    <p>With one of the largest fleet of excavators for hire in South East Queensland, at HBR Heavy Equipment we are proud of our large range of diggers.</p>
    <span class="mini" style="bottom:-16px">&#187;</span>
  </div>

  <div class="tile svc-dark" style="left:456px;top:216px;height:278px">
    <span class="mini" style="top:-18px"><svg width="12" height="12" viewBox="0 0 12 12"><path d="M2 8l4-4 4 4" stroke="#25276f" stroke-width="2" fill="none"/></svg></span>
    We have Makura and Stenfield dozers for hire – in a range of sizes suitable for projects from detailed to bulk earthworks.
    <h3>Dozer Hire</h3>
    <svg style="margin-top:18px" width="80" height="52" viewBox="0 0 80 52" fill="none" stroke="#fff" stroke-width="2.2"><path d="M4 40l10-20 6 2-6 18"/><rect x="24" y="22" width="36" height="14"/><rect x="30" y="8" width="18" height="14"/><rect x="22" y="38" width="44" height="10" rx="5"/></svg>
    <span class="notch-down"></span>
  </div>
  <div class="tile photo" style="left:456px;top:494px;height:274px;background:linear-gradient(160deg,#c9a64a,#6e6650)" role="img" aria-label="Yellow dozer on a gravel pad"></div>

  <div class="tile photo" style="left:747px;top:216px;height:278px;background:linear-gradient(160deg,#6f9ad0,#b99a47 55%,#8a6c44)" role="img" aria-label="Yellow articulated dump truck on site"></div>
  <div class="tile svc-card" style="left:747px;top:494px;height:274px">
    <span class="notch-up"></span>
    <svg width="72" height="48" viewBox="0 0 72 48" fill="none" stroke="#25276f" stroke-width="2.2"><path d="M4 10h44v20H4zM48 16h12l8 10v4H48z"/><circle cx="14" cy="36" r="5"/><circle cx="34" cy="36" r="5"/><circle cx="58" cy="36" r="5"/></svg>
    <h3>Dump Trucks Hire</h3>
    <p>We are South East Queensland's material cartage and haulage specialists, with a range of road registered, track mounted and articulated dump trucks to suit your project require</p>
    <span class="mini" style="bottom:-16px">&#187;</span>
  </div>

  <div class="round" style="left:141px;top:467px;border:2px solid var(--navy)"><svg width="14" height="14" viewBox="0 0 14 14"><path d="M9 2L4 7l5 5" stroke="#25276f" stroke-width="2.4" fill="none"/></svg></div>
  <div class="round navy" style="left:1018px;top:467px"><svg width="14" height="14" viewBox="0 0 14 14"><path d="M5 2l5 5-5 5" stroke="#fff" stroke-width="2.4" fill="none"/></svg></div>
</section>

<!-- clients -->
<h2 class="abs clients-title display">Our Client's</h2>
<div class="abs clients">
  <div class="client">Corvane</div>
  <div class="client"><i></i>Tallis</div>
  <div class="client on">Brightwell</div>
  <div class="client">Norrow</div>
  <div class="client">Kestrel</div>
</div>
<div class="pager" style="left:552px;border-color:var(--navy);color:var(--navy)">&#171;</div>
<div class="pager" style="left:607px;color:#555">&#187;</div>

<!-- contact -->
<section class="abs contact">
  <h2 class="display">Contact us today for a<br><span>free quote</span></h2>
  <div class="info" style="top:260px">
    <span class="ic"><svg width="16" height="20" viewBox="0 0 16 20"><path d="M8 1a6 6 0 0 1 6 6c0 5-6 12-6 12S2 12 2 7a6 6 0 0 1 6-6z" fill="#fff"/><circle cx="8" cy="7" r="2.2" fill="#25276f"/></svg></span>
    <div><h4>LOCATION :</h4><p>12 Ridgeline Rd, Yatala QLD 4207</p></div>
  </div>
  <div class="info" style="top:342px">
    <span class="ic"><svg width="16" height="16" viewBox="0 0 24 24"><path d="M6 2l4 4-2.5 2.5a12 12 0 0 0 8 8L18 14l4 4-3 3C10 21 3 14 3 5z" fill="#fff"/></svg></span>
    <div><h4>PHONE NUMBER :</h4><p>1300 555 019</p></div>
  </div>
  <div class="info" style="top:424px">
    <span class="ic"><svg width="18" height="14" viewBox="0 0 24 18"><rect x="1" y="1" width="22" height="16" fill="#fff"/><path d="M1 1l11 9 11-9" stroke="#25276f" stroke-width="2" fill="none"/></svg></span>
    <div><h4>EMAIL ADDRESS :</h4><p>info@harlowbrentmere.com.au</p></div>
  </div>

  <div class="field" style="left:534px;top:229px;width:259px;height:50px">Frist Name*</div>
  <div class="field" style="left:808px;top:229px;width:262px;height:50px">Last Name*</div>
  <div class="field" style="left:534px;top:298px;width:259px;height:50px">Emai*</div>
  <div class="field" style="left:808px;top:298px;width:262px;height:50px">Phone Number*</div>
  <div class="field" style="left:534px;top:367px;width:536px;height:134px">Enquiry*</div>
  <div class="abs btn-navy" style="left:534px;top:519px;width:143px;height:45px">SUBMIT</div>
</section>

<!-- footer chevron -->
<svg class="abs" style="left:0;top:3518px" width="1200" height="152" viewBox="0 0 1200 152">
  <path d="M0 152 L600 2 L1200 152 Z" fill="#25276f"/>
  <path d="M120 152 L600 22 L1080 152 Z" fill="#fff"/>
  <path d="M170 152 L600 40 L1030 152 Z" fill="#000"/>
</svg>

<footer class="abs footer">
  <div class="abs f-brand">
    <div class="art" role="img" aria-label="White line illustration of a tractor and an excavator"></div>
    <div class="name">HBR Plant Hire</div>
  </div>

  <h5 style="left:384px">QUICK LINKS</h5>
  <ul style="left:387px">
    <li>Home</li><li>About us</li><li>Plant Hire</li><li>Major Project Snapshot</li><li>Policies</li><li>Jobs</li>
  </ul>

  <h5 style="left:592px">CONTACT US</h5>
  <div class="f-row" style="top:96px">
    <span class="ic"><svg width="14" height="18" viewBox="0 0 16 20"><path d="M8 1a6 6 0 0 1 6 6c0 5-6 12-6 12S2 12 2 7a6 6 0 0 1 6-6z" fill="#fff"/><circle cx="8" cy="7" r="2.2" fill="#000"/></svg></span>
    <span>12 Ridgeline Rd, Yatala<br>QLD 4207</span>
  </div>
  <div class="f-row" style="top:158px">
    <span class="ic"><svg width="14" height="14" viewBox="0 0 24 24"><path d="M6 2l4 4-2.5 2.5a12 12 0 0 0 8 8L18 14l4 4-3 3C10 21 3 14 3 5z" fill="#fff"/></svg></span>
    <span>1300 555 019</span>
  </div>
  <div class="f-row" style="top:220px">
    <span class="ic"><svg width="16" height="12" viewBox="0 0 24 18"><rect x="1" y="1" width="22" height="16" fill="#fff"/><path d="M1 1l11 9 11-9" stroke="#000" stroke-width="2" fill="none"/></svg></span>
    <span>info@harlowbrentmere.com.au</span>
  </div>

  <h5 style="left:840px">NEWSLETTER</h5>
  <div class="abs" style="left:843px;top:96px;width:238px;height:37px;background:#fff;color:#333;font-size:14px;padding:9px 12px">Eneter Email</div>
  <div class="abs" style="left:1081px;top:96px;width:44px;height:37px;background:var(--navy);display:flex;align-items:center;justify-content:center">
    <svg width="16" height="16" viewBox="0 0 16 16"><path d="M1 7l14-6-5 14-2-6z" fill="#fff"/></svg>
  </div>
  <span class="social" style="left:831px" aria-label="Social link"></span>
  <span class="social on" style="left:864px" aria-label="Social link"></span>
  <span class="social" style="left:907px" aria-label="Social link"></span>
  <span class="social" style="left:948px" aria-label="Social link"></span>

  <div class="abs" style="left:107px;top:300px;width:1005px;height:1px;background:#333"></div>
  <p class="copy">© 2024 Harlow Brentmere | All rights reserved.</p>
</footer>

</body>
</html>
```